American cannabis tech company business card design

Pavrel.com is seeking a modern, professional, and brand-aligned business card that represents our company and its core values: Mission, Story, Values, and Impact. As an innovative cannabis company, we want a business card that is not only visually appealing but also serves as a representation of who we are and what we stand for.

Project Scope: Design a double-sided business card that integrates our brand identity and core values. Incorporate our key brand elements, ensuring a sleek and contemporary aesthetic. Visually reflect our core values (Mission, Story, Values, Impact) in a way that is engaging yet professional.

Target Market(s)

Vendors, third parties,

Contact Information for Business Card

Contact details (name, title, email, phone, website, etc.)

Font styles to use
Other font styles liked:
• Caslon, Centra

Colors

Designer to choose colors to be used in the design.

Requirements
Must have
• Pavrel.com logo and branding A creative yet clean way to integrate our core values (Mission, Story, Values, Impact) Modern typography and a well-structured layout
Nice to have
• forest green, grey, white, black
Should not have
• references to marijuana, leafs, plants, or related product

```html
<!DOCTYPE html>
<html lang="en">
<head>
<meta charset="UTF-8">
<title>Pavrel.com Business Card</title>
<link rel="stylesheet" href="https://fonts.googleapis.com/css2?family=Libre+Caslon+Text:wght@400;700&display=swap">
<style>
  :root {
    --forest: #173019;
    --forest-deep: #122815;
    --muted-green: #4f7a52;
    --paper: #ffffff;
    --paper-shade: #eeeeee;
    --stage: #e4e4e2;
    --line: rgba(255, 255, 255, 0.18);
  }
  * { box-sizing: border-box; margin: 0; padding: 0; }
  html, body {
    width: 1200px;
    height: 900px;
    overflow: hidden;
    background: var(--stage);
    font-family: "Libre Caslon Text", Georgia, serif;
  }
  .stage {
    position: relative;
    width: 1200px;
    height: 900px;
  }
  .card {
    position: absolute;
    left: 280px;
    width: 640px;
    height: 366px;
    border-radius: 36px;
    box-shadow: 0 10px 24px rgba(0, 0, 0, 0.18);
  }
  .card-front {
    top: 70px;
    background: linear-gradient(135deg, var(--paper) 40%, var(--paper-shade));
    display: flex;
    align-items: center;
    justify-content: center;
  }
  .card-back {
    top: 464px;
    background: linear-gradient(160deg, var(--forest) 0%, var(--forest-deep) 100%);
    color: var(--paper);
    text-align: center;
  }
  .wordmark {
    font-weight: 700;
    letter-spacing: 2px;
    line-height: 1;
  }
  .card-front .wordmark {
    color: var(--forest);
    font-size: 92px;
  }
  .card-back .wordmark {
    color: var(--paper);
    font-size: 84px;
    position: absolute;
    top: 62px;
    left: 0;
    right: 0;
  }
  .holder {
    position: absolute;
    top: 186px;
    left: 0;
    right: 0;
  }
  .holder-name {
    font-size: 19px;
    font-weight: 700;
    letter-spacing: 1px;
    text-transform: uppercase;
    color: var(--muted-green);
  }
  .holder-title {
    margin-top: 4px;
    font-size: 16px;
  }
  .divider {
    position: absolute;
    left: 120px;
    right: 120px;
    height: 1px;
    background: var(--line);
  }
  .divider-top { top: 178px; }
  .divider-bottom { top: 258px; }
  .contact {
    position: absolute;
    top: 272px;
    left: 0;
    right: 0;
    font-size: 15px;
  }
  .contact-row {
    display: flex;
    align-items: center;
    justify-content: center;
    gap: 8px;
  }
  .contact-row svg { width: 14px; height: 14px; fill: var(--muted-green); }
  .website {
    margin-top: 8px;
    letter-spacing: 5px;
    font-size: 14px;
  }
</style>
</head>
<body>
<main class="stage">
  <section class="card card-front">
    <div class="wordmark">PAVREL</div>
  </section>

  <section class="card card-back">
    <div class="wordmark">PAVREL</div>
    <div class="divider divider-top"></div>
    <div class="holder">
      <p class="holder-name">Owen Hartley</p>
      <p class="holder-title">Co-founder &amp; CEO</p>
    </div>
    <div class="divider divider-bottom"></div>
    <div class="contact">
      <p class="contact-row">
        <svg viewBox="0 0 24 24" aria-hidden="true"><path d="M6.6 10.8a15.1 15.1 0 0 0 6.6 6.6l2.2-2.2c.3-.3.7-.4 1-.2 1.1.4 2.3.6 3.6.6.6 0 1 .4 1 1V20c0 .6-.4 1-1 1A17 17 0 0 1 3 4c0-.6.4-1 1-1h3.5c.6 0 1 .4 1 1 0 1.3.2 2.5.6 3.6.1.3 0 .7-.2 1z"/></svg>
        <span>000-000-0000</span>
        <span>|</span>
        <svg viewBox="0 0 24 24" aria-hidden="true"><path d="M2 5h20v14H2zm2 2v.5l8 5 8-5V7l-8 5z"/></svg>
        <span>owen@pavrel.com</span>
      </p>
      <p class="website">www.pavrel.com</p>
    </div>
  </section>
</main>
</body>
</html>
```